Postcard Design Project A Healthy reminder

Dr.'s Dhelpit and Sirel dunwat. Internal Medicine/Family practice. This postcard will be for our patients that we have not seen in a while. Also we need another postcard (the one your designing) with a different heading for New patient's. Do you offer a price break for that? The only thing we would need to change is the heading. Please let me know. Thank you so much! Also can you use the map on the last postcard and our logo I made? I cant find it. Please feel free to call me or email me.

```html
<!DOCTYPE html>
<html lang="en">
<head>
<meta charset="utf-8">
<title>A Healthy Reminder – Postcard</title>
<link href="https://fonts.googleapis.com/css2?family=Tinos:wght@400;700&display=swap" rel="stylesheet">
<style>
  :root{
    --red:#a30a10;
    --red-dark:#7d050a;
    --ink:#161616;
    --paper:#ffffff;
    --paper-soft:#f1f1f1;
    --steel:#b9b9b9;
    --backdrop:#6b6b6b;
  }
  *{margin:0;padding:0;box-sizing:border-box}
  html,body{width:880px;height:1200px;overflow:hidden}
  body{background:var(--backdrop);font-family:"Tinos","Times New Roman",serif;color:var(--ink);position:relative}
  .card{position:absolute;background:var(--paper);overflow:hidden}
  .card svg.art{position:absolute;inset:0;width:100%;height:100%}
  .front{left:53px;top:56px;width:773px;height:526px}
  .back{left:46px;top:620px;width:786px;height:534px}

  /* front */
  .brand{position:absolute;left:62px;top:62px;width:220px;display:flex;flex-direction:column;align-items:center}
  .brand-row{display:flex;align-items:center;gap:10px}
  .brand-mark{width:22px;height:22px;border:2px solid var(--ink)}
  .brand-name{font-size:17px;font-weight:700;color:var(--ink)}
  .brand-tag{margin-top:14px;font-size:10px;letter-spacing:1px;font-weight:700;color:var(--ink)}
  .headline{position:absolute;left:50px;top:158px;line-height:1}
  .headline .lead{font-size:29px;display:block;margin-bottom:6px}
  .headline .lead b{color:var(--red)}
  .headline .big{display:block;font-weight:700;font-size:76px;letter-spacing:-1px;line-height:0.78}
  .headline .big.red{color:var(--red)}
  .contact{position:absolute;left:50px;top:390px;color:var(--paper)}
  .contact .line{display:flex;align-items:flex-start;gap:8px;font-size:17px;line-height:21px}
  .contact .phone{font-size:33px;font-weight:700;margin-top:10px;align-items:center;gap:12px}
  .contact .web{margin-top:6px;align-items:center}
  .contact svg{flex:none}

  /* back */
  .doctors{position:absolute;left:40px;top:34px;font-size:30px;line-height:40px;font-weight:700;color:var(--red)}
  .doctors span{font-weight:400;color:var(--ink)}
  .call{position:absolute;left:40px;top:303px;color:var(--paper);font-weight:700;font-size:34px;line-height:40px;letter-spacing:0.5px}
  .social{position:absolute;left:40px;top:412px;font-size:12px;font-weight:700;display:flex;align-items:center;gap:10px}
  .social .dot{width:18px;height:18px;border-radius:50%;background:#3b5a98}
  .social-url{position:absolute;left:40px;top:436px;font-size:15px}
  .social-url b{color:var(--red)}
  .located{position:absolute;left:40px;top:462px;font-size:17px;line-height:21px}
  .stamp{position:absolute;left:647px;top:38px;width:94px;height:94px;border:1px solid #555}
  .address-line{position:absolute;left:540px;width:201px;height:0;border-top:1.5px solid #333}
</style>
</head>
<body>

<section class="card front">
  <svg class="art" viewBox="0 0 773 526" aria-hidden="false">
    <defs>
      <linearGradient id="photoTone" x1="0" y1="0" x2="1" y2="1">
        <stop offset="0" stop-color="#cdb7a0"/>
        <stop offset="0.5" stop-color="#e3ddd6"/>
        <stop offset="1" stop-color="#b9b3ad"/>
      </linearGradient>
    </defs>
    <rect width="773" height="526" fill="var(--paper-soft)"/>
    <path d="M0 380 C150 340 330 345 400 400 C430 440 450 490 480 526 L0 526 Z" fill="var(--red)"/>
    <path d="M398 0 C318 130 322 400 470 526 L500 526 C350 400 345 120 432 0 Z" fill="var(--red)"/>
    <path d="M420 0 C340 125 340 400 488 526 L500 526 C352 400 350 120 432 0 Z" fill="var(--steel)"/>
    <path role="img" aria-label="Photo of two doctors in white coats reviewing a chart in a clinic hallway" d="M432 0 C350 120 352 400 500 526 L773 526 L773 0 Z" fill="url(#photoTone)"/>
  </svg>

  <div class="brand">
    <div class="brand-row"><span class="brand-mark"></span><span class="brand-name">Dhelpit T Dunwat, M.D.</span></div>
    <div class="brand-tag">A Primary Care Office</div>
  </div>

  <h1 class="headline">
    <span class="lead">A healthy <b>reminder,</b></span>
    <span class="lead">It is time for your</span>
    <span class="big">annual</span>
    <span class="big red">exam.</span>
  </h1>

  <div class="contact">
    <div class="line">
      <svg width="14" height="18" viewBox="0 0 14 18"><circle cx="7" cy="6" r="4" fill="none" stroke="#fff" stroke-width="1.6"/><path d="M7 10 L7 15 M2 16 H12" stroke="#fff" stroke-width="1.6"/></svg>
      <span>4825 N. Harlow Street Suite 210<br>Carvale, Ca 90120</span>
    </div>
    <div class="line phone">
      <svg width="28" height="28" viewBox="0 0 28 28"><circle cx="14" cy="14" r="12.5" fill="none" stroke="#fff" stroke-width="2"/><path d="M10 8 C8 10 9 14 12 17 C15 20 18 21 20 19 L18 16.5 L16 17.5 C14.5 16.5 11.5 13.5 10.5 12 L11.5 10 Z" fill="#fff"/></svg>
      <span>(555) 014-2890</span>
    </div>
    <div class="line web">
      <svg width="14" height="14" viewBox="0 0 14 14"><circle cx="7" cy="7" r="6" fill="none" stroke="#fff" stroke-width="1.3"/><ellipse cx="7" cy="7" rx="2.6" ry="6" fill="none" stroke="#fff" stroke-width="1.1"/><path d="M1 7 H13" stroke="#fff" stroke-width="1.1"/></svg>
      <span>www.dhelpitdunwatmd.com</span>
    </div>
  </div>
</section>

<section class="card back">
  <svg class="art" viewBox="0 0 786 534">
    <defs>
      <linearGradient id="panelTone" x1="0" y1="0" x2="0" y2="1">
        <stop offset="0" stop-color="#ececec"/>
        <stop offset="1" stop-color="#fafafa"/>
      </linearGradient>
      <clipPath id="panelClip">
        <path d="M0 0 L285 0 C410 90 425 300 268 534 L0 534 Z"/>
      </clipPath>
    </defs>
    <path d="M0 0 L300 0 C430 80 460 300 290 534 L0 534 Z" fill="var(--red)"/>
    <path d="M0 0 L290 0 C418 85 440 300 276 534 L0 534 Z" fill="var(--steel)"/>
    <path d="M0 0 L285 0 C410 90 425 300 268 534 L0 534 Z" fill="url(#panelTone)"/>
    <g clip-path="url(#panelClip)">
      <rect role="img" aria-label="Street map showing the office location" x="10" y="122" width="400" height="168" fill="#dfe6dc"/>
      <rect x="0" y="290" width="400" height="106" fill="var(--red)"/>
    </g>
    <circle cx="392" cy="314" r="94" fill="var(--red)"/>
    <circle role="img" aria-label="Photo of the office entrance with trees and lawn" cx="392" cy="314" r="86" fill="#8b9a6a"/>
  </svg>

  <h2 class="doctors">Dr.'s Dhelpit <span>and</span><br>Sirel dunwat</h2>

  <div class="call">CALL NOW<br>(555) 014-2890</div>

  <div class="social">VISIT US ON <span class="dot"></span></div>
  <div class="social-url">www.socialpage.com/<b>doctorsnearby</b></div>
  <div class="located">Located On The<br><b>SE corner of Harlow and Benning.</b></div>

  <div class="stamp"></div>
  <div class="address-line" style="top:286px"></div>
  <div class="address-line" style="top:333px"></div>
  <div class="address-line" style="top:380px"></div>
</section>

</body>
</html>
```